Brightline Energy Product Distribution Brochure

We are looking to have our current brochure for our customers completely redesigned...the idea is to present the relevant information in an attractive way . Our website is brightlineenergyco.example where you can find more information about us. We have included a file with a rough idea of the page order and what each should include but feel free to adapt based on design. The example provided is only for context and doesnt have to be maintained. We will be using the brochure both digitally and in print form. As long as it reads easily and is eye catching, the design can be horizontal or vertical.Final deliverable should be indesign file.

"Our Brands" page: should be limited to one page (space being enough) where it has the header for each one (for example diesel generators) space for one or two lines of text and then the corresponding logos for each of the five categories
Updates

For those asking: the "our brands" page should be a single page layout where there is a header with the corresponding section and space for maybe one line of text followed by the two logos for that category. Each of the product pages should be similar in fashion to the one in the document attached: a photo of the product with some white space and space for the text to be included. We will be posting additional examples today

Target Market(s)

We want to present it to customers both digitally and in print so they can see our products

Industry/Entity Type

Power Generation

Font styles to use
Serif

Requirements
Must have
• Eye catching and able to present the information in a presentable fashion. Rest is up to you.
Nice to have
• Should incorporate the colors of our logo but can also add other depending on design

```html
<!DOCTYPE html>
<html lang="en">
<head>
<meta charset="utf-8">
<title>Brightline Energy – Distributor Program Guide</title>
<link href="https://fonts.googleapis.com/css2?family=Montserrat:wght@500;600;700;800;900&family=Open+Sans:wght@400;600&display=swap" rel="stylesheet">
<style>
:root{
  --board:#d3d4d6;
  --paper:#ffffff;
  --gold:#f6b70b;
  --ink:#2c2c2e;
  --text:#5a5a5a;
  --strip:#3b3b3d;
  --red:#c0282d;
}
*{box-sizing:border-box;margin:0;padding:0}
html,body{width:955px;height:1200px;overflow:hidden}
body{background:var(--board);font-family:"Open Sans",sans-serif;color:var(--text);position:relative}
.page{position:absolute;width:202px;height:260px;background:var(--paper);overflow:hidden}
.strip{position:absolute;left:0;right:0;bottom:0;height:3px;background:var(--strip)}
.pn{position:absolute;bottom:0;width:10px;height:7px;background:var(--gold);color:var(--ink);font:700 3.5px/7px Montserrat,sans-serif;text-align:center}
.pn.l{left:2px}.pn.r{right:2px}
.abs{position:absolute}
.gold{background:var(--gold)}
.photo-plant{background:linear-gradient(180deg,#24314f 0%,#3d4e72 22%,#8a7a5e 42%,#e9a632 58%,#f3c25a 66%,#6b4a1d 82%,#2a2420 100%)}
.photo-tower{background:linear-gradient(180deg,#1d3a72 0%,#2f5592 35%,#5b6f8c 55%,#d79a35 75%,#f0b84a 85%,#3a2a16 100%)}
.photo-grid{background:linear-gradient(180deg,#16305f 0%,#2f5aa0 38%,#7c8fb4 55%,#f0a540 68%,#c27a22 78%,#1f1a14 100%)}
.photo-gold{background:linear-gradient(160deg,#2b2c38 0%,#5a4a2e 30%,#d99a2a 55%,#f6c54a 68%,#7a5520 85%,#1d1d22 100%)}
.photo-steel{background:linear-gradient(160deg,#41577a 0%,#7d93b0 35%,#c6ced6 55%,#8e9aa6 75%,#3e4a5a 100%)}
.photo-sunset{background:linear-gradient(180deg,#6b86aa 0%,#a7b4c2 35%,#e4c26a 55%,#f3b63a 65%,#3c3b3e 85%,#25262a 100%)}
.photo-gear{background:radial-gradient(circle at 35% 45%,#ffe07a 0%,#e6ae2a 30%,#a97a24 55%,#8d8b86 80%,#c9c9c9 100%)}
.photo-warehouse{background:linear-gradient(160deg,#3a4a5e 0%,#6b7d92 40%,#a98d5e 70%,#4c3e2c 100%)}
.photo-boxes{background:linear-gradient(160deg,#8c6a3e 0%,#b8905a 40%,#cdb48a 60%,#5a5f6a 100%)}
.photo-room{background:linear-gradient(170deg,#5f5848 0%,#9a8a62 40%,#d2b260 60%,#6a5a3a 100%)}
.prod{background:linear-gradient(160deg,#ffffff 0%,#eeeeee 55%,#cfcfcf 100%)}
.prod-base{background:#2b2b2d}
.prod-dark{background:linear-gradient(160deg,#5a5d62,#1e1f22)}
.prod-board{background:linear-gradient(160deg,#3a5684,#1a2741)}
.kicker{font:600 6px/1.1 Montserrat,sans-serif;color:var(--ink);letter-spacing:.2px}
.title{font:800 8.5px/1.1 Montserrat,sans-serif;color:var(--gold);letter-spacing:.3px}
.title-dark{font:900 8.5px/1.05 Montserrat,sans-serif;color:var(--ink)}
.sub{font:600 6.5px/1.15 Montserrat,sans-serif;color:var(--ink);letter-spacing:.3px}
.label{font:600 3.3px/1.2 Montserrat,sans-serif;color:var(--gold);text-transform:uppercase;letter-spacing:.2px}
.copy{font-size:3.1px;line-height:1.4;color:var(--text)}
.list{list-style:none;font-size:3px;line-height:1.45;color:var(--text)}
.list li::before{content:"";display:inline-block;width:1.6px;height:1.6px;background:var(--gold);margin:0 1.5px .4px 0}
.brandname{font:700 4.4px/1 Montserrat,sans-serif;color:var(--ink);white-space:nowrap}
.mark{display:inline-block;width:4.5px;height:4.5px;background:var(--gold);vertical-align:-.5px;margin-right:1.5px}
.kw{position:absolute;font:700 3.3px/1 Montserrat,sans-serif;color:var(--ink)}
.index-list{list-style:none}
.index-list li{display:flex;justify-content:space-between;align-items:center;height:5.1px;font:600 3px/1 Montserrat,sans-serif;color:var(--ink);white-space:nowrap}
.index-list li.sub1{padding-left:4px}
.index-list li.sub2{padding-left:9px;font-weight:500}
.index-list .num{color:var(--gold);font:700 5px/1 Montserrat,sans-serif}
</style>
</head>
<body>

<!-- Cover -->
<section class="page cover" style="left:60px;top:64px">
  <div class="abs gold" style="left:140px;top:0;width:62px;height:66px;clip-path:polygon(14% 0,100% 0,100% 100%,62% 100%)"></div>
  <h1 class="title-dark abs" style="left:16px;top:14px">DISTRIBUTOR<br>PROGRAM GUIDE</h1>
  <p class="abs" style="left:16px;top:40px;font:600 4.6px/1.2 Montserrat,sans-serif;color:var(--ink)">DIESEL GENERATORS<br>ALTERNATORS &amp; PARTS</p>
  <div class="abs photo-plant" style="left:0;top:66px;width:202px;height:124px" role="img" aria-label="Industrial power plant at dusk"></div>
  <div class="abs gold" style="left:0;top:190px;width:202px;height:70px;clip-path:polygon(0 0,100% 0,100% 12%,72% 12%,50% 100%,0 100%)"></div>
  <p class="abs" style="left:13px;top:232px;font:700 4px/1 Montserrat,sans-serif;color:var(--ink)">1-800-555-0142</p>
  <p class="abs" style="left:13px;top:240px;font-size:3px;color:var(--ink)">www.brightlineenergyco.example</p>
  <div class="abs brandname" style="left:124px;top:226px;color:var(--gold)"><span class="mark"></span>BRIGHTLINE ENERGY</div>
</section>

<!-- Index -->
<section class="page index" style="left:272px;top:64px">
  <div class="abs photo-tower" style="left:0;top:0;width:78px;height:260px" role="img" aria-label="Refinery towers lit at night"></div>
  <div class="abs gold" style="left:78px;top:0;width:124px;height:98px;clip-path:polygon(0 0,100% 0,100% 100%,0 80%)"></div>
  <h2 class="title-dark abs" style="left:102px;top:128px;font-size:8px">INDEX</h2>
  <ol class="index-list abs" style="left:102px;top:143px;width:80px">
    <li>ABOUT OUR COMPANY<span class="num">03</span></li>
    <li>OUR BRANDS<span class="num">04</span></li>
    <li>OUR STOCK<span class="num">05</span></li>
    <li>OUR PRODUCTS<span class="num">06</span></li>
    <li class="sub1">DIESEL GENERATORS<span class="num">06</span></li>
    <li class="sub2">STANDBY GENERATORS</li>
    <li class="sub2">PRIME GENERATORS</li>
    <li class="sub2">RENTAL GENERATORS</li>
    <li class="sub1">AC ALTERNATORS<span class="num">09</span></li>
    <li class="sub1">ALTERNATOR PARTS<span class="num">10</span></li>
    <li class="sub1">CONTROLLERS<span class="num">11</span></li>
    <li class="sub1">TRANSFER SWITCHES<span class="num">12</span></li>
    <li>OUR DISTRIBUTORS<span class="num">13</span></li>
  </ol>
  <div class="strip"></div><div class="pn l">01</div>
</section>

<!-- About -->
<section class="page about" style="left:474px;top:64px">
  <div class="abs gold" style="left:150px;top:0;width:52px;height:72px;clip-path:polygon(40% 0,100% 0,100% 100%,0 100%)"></div>
  <p class="kicker abs" style="left:20px;top:20px">ABOUT</p>
  <h2 class="title abs" style="left:20px;top:28px">BRIGHTLINE ENERGY</h2>
  <p class="abs" style="left:20px;top:42px;font:600 3.6px/1.3 Montserrat,sans-serif;color:var(--ink)">PARTNER WITH A RELIABLE,<br>INNOVATIVE SINGLE SOURCE<br>OF PREMIUM QUALITY POWER<br>GENERATION PRODUCTS</p>
  <div class="abs photo-grid" style="left:0;top:72px;width:202px;height:96px" role="img" aria-label="Power station and transmission lines at twilight"></div>
  <p class="copy abs" style="left:20px;top:174px;width:78px">With over twenty years in power generation we supply diesel generators, alternators, parts and controls to dealers across the region. Our team offers broad stock, fast quotes and practical advice so every project moves quickly. We back each order with clear pricing, same day shipping and real support from people who know the equipment well.</p>
  <p class="copy abs" style="left:104px;top:174px;width:80px">Customers rely on our catalogue, training and technical service to keep sites running. As an authorized partner for leading makers we bring engines, alternators and switches together under one roof. We aim to be the single source that makes sourcing power equipment simple, dependable and fast for every distributor we serve.</p>
  <div class="strip"></div><div class="pn r">01</div>
</section>

<!-- Our Brand -->
<section class="page brands" style="left:60px;top:334px">
  <div class="abs photo-plant" style="left:0;top:0;width:202px;height:30px" role="img" aria-label="Industrial plant skyline"></div>
  <h2 class="title-dark abs" style="left:15px;top:52px;font-size:8px">OUR BRAND</h2>
  <div class="abs" style="left:15px;top:74px;width:180px">
    <div style="height:36px;position:relative">
      <p class="label">Diesel Generators</p>
      <p class="copy" style="width:82px">Trusted engine sets for standby and prime power, supplied new with full factory backing.</p>
      <div class="abs" style="left:104px;top:6px;line-height:6px"><span class="brandname" style="font-size:3.4px;color:var(--gold)"><span class="mark" style="width:3px;height:3px"></span>Brightline</span> <span class="brandname">NORVIK</span><br><span class="brandname" style="margin-left:30px">VELTRA</span></div>
    </div>
    <div style="height:36px;position:relative">
      <p class="label">AC Alternators</p>
      <p class="copy" style="width:82px">Brushless alternators in a wide range of frames, ready to ship from local stock.</p>
      <div class="abs" style="left:110px;top:4px;line-height:6px"><span class="brandname" style="color:var(--red);font-size:3.6px">HALDEN</span> <span class="brandname" style="color:var(--red);font-size:3.6px">TORVEL</span><br><span class="brandname">ARCAND</span></div>
    </div>
    <div style="height:36px;position:relative">
      <p class="label">Alternator Parts</p>
      <p class="copy" style="width:82px">Regulators, diodes and rotating parts kept on hand for quick repairs.</p>
      <div class="abs" style="left:110px;top:4px;line-height:6px"><span class="brandname" style="color:var(--red);font-size:3.6px">HALDEN</span> <span class="brandname" style="color:var(--red);font-size:3.6px">TORVEL</span><br><span class="brandname">ARCAND</span></div>
    </div>
    <div style="height:36px;position:relative">
      <p class="label">Controls</p>
      <p class="copy" style="width:82px">Digital controllers for single sets, paralleling and remote monitoring.</p>
      <div class="abs" style="left:104px;top:8px"><span class="brandname">KESTREL</span> <span class="brandname">VELTRA</span></div>
    </div>
    <div style="height:36px;position:relative">
      <p class="label">Transfer Switches</p>
      <p class="copy" style="width:82px">Automatic transfer switches from 100 to 2000 amps for every load.</p>
      <div class="abs" style="left:104px;top:8px"><span class="brandname" style="color:var(--red)">BRENNAN</span> <span class="brandname">MERIDIAN</span></div>
    </div>
  </div>
  <div class="strip"></div><div class="pn l">01</div>
</section>

<!-- Our Stock -->
<section class="page stock" style="left:262px;top:334px">
  <div class="abs gold" style="left:168px;top:0;width:34px;height:54px"></div>
  <div class="abs prod-dark" style="left:124px;top:12px;width:42px;height:50px" role="img" aria-label="Generator control panel"></div>
  <h2 class="title-dark abs" style="left:12px;top:18px;font-size:8px">OUR STOCK</h2>
  <p class="abs" style="left:12px;top:32px;font:600 3.6px/1.3 Montserrat,sans-serif;color:var(--ink)">COST, LEAD TIME, LOGISTICS AND<br>MANY CHALLENGES</p>
  <p class="copy abs" style="left:12px;top:42px;width:100px">LUCKILY YOU JUST FOUND BRIGHTLINE ENERGY<br><span style="color:var(--gold)">A SINGLE SOURCE SOLUTION</span></p>
  <div class="abs photo-warehouse" style="left:12px;top:76px;width:56px;height:54px" role="img" aria-label="Technicians working in a warehouse"></div>
  <ul class="list abs" style="left:74px;top:80px;width:116px">
    <li>A+ rating with leading business bureaus</li>
    <li>Decades of combined industry experience</li>
    <li>Countries served around the world</li>
    <li>Sales and engineering staff certified</li>
    <li>Orders fulfilled each year</li>
    <li>Products shipped in the past year</li>
    <li>Yearly sales and growing</li>
  </ul>
  <p class="label abs" style="left:12px;top:136px">We share your urgency,</p>
  <p class="copy abs" style="left:12px;top:140px;width:104px">SO WE BECAME EXCELLENT AT SAME DAY.</p>
  <ul class="list abs" style="left:12px;top:148px;width:104px">
    <li>Generator trailers from 1500 to 10000 lbs in stock</li>
    <li>Fuel tanks from 50 to 1000 gal in stock</li>
    <li>Transfer switches from 100 to 2000 amps</li>
    <li>Diesel generators from 10 to 500 kW in stock</li>
    <li>Engine parts, alternator parts and controls</li>
  </ul>
  <p class="copy abs" style="left:12px;top:190px;width:104px">Brightline Energy offers one of the largest inventories in the region, with parts most needed in urgent repairs. We also carry a deep stock of regulators and switches to reach any site quickly.</p>
  <div class="abs photo-boxes" style="left:122px;top:134px;width:68px;height:68px" role="img" aria-label="Worker checking boxes in a stock room"></div>
  <div class="abs gold" style="left:122px;top:206px;width:68px;height:16px;padding:3px;font:700 3.2px/1.4 Montserrat,sans-serif;color:var(--ink)">we will quote same day and<br>we will ship SAME DAY.</div>
  <div class="strip"></div><div class="pn r">01</div>
</section>

<!-- Standby -->
<section class="page standby" style="left:474px;top:334px">
  <p class="kicker abs" style="left:14px;top:18px">OUR PRODUCT</p>
  <h2 class="title abs" style="left:14px;top:30px">DIESEL GENERATORS</h2>
  <p class="sub abs" style="left:14px;top:52px">STANDBY<br>GENERATORS</p>
  <div class="abs photo-gold" style="left:0;top:96px;width:70px;height:164px;clip-path:polygon(0 10%,100% 0,80% 100%,0 100%)" role="img" aria-label="Refinery structure lit in gold"></div>
  <div class="abs prod" style="left:84px;top:58px;width:100px;height:58px" role="img" aria-label="White enclosed diesel generator"></div>
  <div class="abs prod-base" style="left:84px;top:116px;width:100px;height:6px"></div>
  <span class="kw" style="left:171px;top:60px">100 KW</span>
  <p class="label abs" style="left:88px;top:138px">Features</p>
  <ul class="list abs" style="left:88px;top:144px;width:104px">
    <li>30 to 500 kW diesel engine sets</li>
    <li>Brushless alternator with AVR option</li>
    <li>Digital controller for standalone use</li>
    <li>Steel enclosure with sound lining</li>
    <li>Main line circuit breaker</li>
    <li>Single-wall base fuel tank</li>
    <li>Battery disconnect switch</li>
    <li>12V starting battery</li>
  </ul>
  <div class="strip"></div><div class="pn l">01</div>
</section>

<!-- Prime -->
<section class="page prime" style="left:676px;top:334px">
  <div class="abs gold" style="left:80px;top:0;width:122px;height:40px;clip-path:polygon(20% 0,100% 0,100% 100%,0 100%)"></div>
  <p class="kicker abs" style="right:14px;top:18px;text-align:right">OUR PRODUCT</p>
  <h2 class="title abs" style="right:14px;top:30px;text-align:right">DIESEL GENERATORS</h2>
  <p class="sub abs" style="right:14px;top:52px;text-align:right">PRIME<br>GENERATORS</p>
  <div class="abs photo-gold" style="left:132px;top:96px;width:70px;height:164px;clip-path:polygon(0 0,100% 10%,100% 100%,20% 100%)" role="img" aria-label="Refinery structure lit in gold"></div>
  <div class="abs prod" style="left:12px;top:58px;width:100px;height:58px" role="img" aria-label="White enclosed diesel generator"></div>
  <div class="abs prod-base" style="left:12px;top:116px;width:100px;height:6px"></div>
  <span class="kw" style="left:98px;top:60px">100 KW</span>
  <p class="label abs" style="left:14px;top:138px">Features</p>
  <ul class="list abs" style="left:14px;top:144px;width:104px">
    <li>30 to 500 kW diesel engine sets</li>
    <li>Brushless alternator with AVR option</li>
    <li>Digital controller for standalone use</li>
    <li>Steel enclosure with sound lining</li>
    <li>Main line circuit breaker</li>
    <li>Single-wall base fuel tank</li>
    <li>Battery disconnect switch</li>
    <li>12V starting battery</li>
  </ul>
  <div class="strip"></div><div class="pn r">01</div>
</section>

<!-- Rental -->
<section class="page rental" style="left:60px;top:610px">
  <p class="kicker abs" style="left:14px;top:18px">OUR PRODUCT</p>
  <h2 class="title abs" style="left:14px;top:30px">DIESEL GENERATORS</h2>
  <p class="sub abs" style="left:14px;top:52px">RENTAL<br>GENERATORS</p>
  <div class="abs photo-gold" style="left:0;top:96px;width:70px;height:164px;clip-path:polygon(0 10%,100% 0,80% 100%,0 100%)" role="img" aria-label="Refinery structure lit in gold"></div>
  <div class="abs prod" style="left:84px;top:58px;width:100px;height:58px" role="img" aria-label="White enclosed diesel generator"></div>
  <div class="abs prod-base" style="left:84px;top:116px;width:100px;height:6px"></div>
  <span class="kw" style="left:171px;top:60px">100 KW</span>
  <p class="label abs" style="left:88px;top:138px">Features</p>
  <ul class="list abs" style="left:88px;top:144px;width:104px">
    <li>30 to 500 kW diesel engine sets</li>
    <li>Brushless alternator with AVR option</li>
    <li>Digital controller for standalone use</li>
    <li>Steel enclosure with sound lining</li>
    <li>Main line circuit breaker</li>
    <li>Single-wall base fuel tank</li>
    <li>Battery disconnect switch</li>
    <li>12V starting battery</li>
  </ul>
  <div class="strip"></div><div class="pn l">01</div>
</section>

<!-- AC Alternators -->
<section class="page alternators" style="left:262px;top:610px">
  <div class="abs photo-gold" style="left:0;top:0;width:202px;height:100px" role="img" aria-label="Industrial plant with storage tanks"></div>
  <div class="abs gold" style="left:170px;top:0;width:32px;height:100px"></div>
  <div class="abs prod-dark" style="left:92px;top:40px;width:90px;height:78px;border-radius:30px 6px 6px 30px" role="img" aria-label="Black AC alternator unit"></div>
  <p class="kicker abs" style="left:16px;top:110px">OUR PRODUCT</p>
  <h2 class="title abs" style="left:16px;top:122px">AC ALTERNATORS</h2>
  <p class="label abs" style="left:16px;top:150px">Description</p>
  <p class="copy abs" style="left:16px;top:158px;width:80px">Brushless alternators from small frames to large industrial units, built for standby and continuous duty. Each model ships tested with voltage regulator, clear wiring and full documentation so installers can commission quickly and safely on any site.</p>
  <p class="copy abs" style="left:104px;top:158px;width:82px">We stock single and three phase models with a range of windings and mounting options. Our team helps match frame size, output and enclosure to the engine and load, keeping lead times short and repairs simple for every dealer.</p>
  <div class="strip"></div><div class="pn r">01</div>
</section>

<!-- Alternator Parts -->
<section class="page parts" style="left:474px;top:610px">
  <p class="kicker abs" style="left:12px;top:18px">OUR PRODUCT</p>
  <h2 class="title abs" style="left:12px;top:32px">ALTERNATOR PARTS</h2>
  <div class="abs prod-board" style="left:14px;top:50px;width:66px;height:62px" role="img" aria-label="Voltage regulator circuit board"></div>
  <div class="abs prod" style="left:104px;top:48px;width:70px;height:56px;box-shadow:0 0 0 .5px #bbb" role="img" aria-label="Regulator module in a grey housing"></div>
  <p class="label abs" style="left:12px;top:120px">Product Name</p>
  <p class="copy abs" style="left:12px;top:125px;width:82px">Automatic voltage regulator for brushless alternators, with quick setup, stable output and wide range sensing.</p>
  <p class="label abs" style="left:12px;top:148px">Features</p>
  <p class="copy abs" style="left:12px;top:153px;width:82px">Compact board with sealed parts, simple trim controls and protection against overload. Suited to new builds and field repairs alike, with full wiring guide and local stock for quick shipping to your site.</p>
  <p class="label abs" style="left:104px;top:110px">Product Name</p>
  <p class="copy abs" style="left:104px;top:115px;width:86px">Regulator module in a rugged housing, made for generator panels that need steady voltage under load.</p>
  <p class="label abs" style="left:104px;top:148px">Features</p>
  <p class="copy abs" style="left:104px;top:153px;width:86px">Panel mounted design with clear terminals and adjustable gain. Tested before shipping and backed by our service team, with spares held in stock for fast repair work on every common frame.</p>
  <div class="strip"></div><div class="pn l">01</div>
</section>

<!-- Controllers -->
<section class="page controllers" style="left:676px;top:610px">
  <div class="abs photo-gear" style="left:0;top:0;width:202px;height:100px" role="img" aria-label="Close-up of golden gears"></div>
  <div class="abs prod-dark" style="left:98px;top:38px;width:96px;height:64px;border-radius:3px" role="img" aria-label="Digital generator controller with display"></div>
  <p class="kicker abs" style="left:18px;top:110px">OUR PRODUCT</p>
  <h2 class="title abs" style="left:18px;top:122px">CONTROLLERS</h2>
  <p class="label abs" style="left:18px;top:150px">Description</p>
  <p class="copy abs" style="left:18px;top:156px;width:80px">Digital controllers for start, stop and protection of diesel sets. Clear displays, simple menus and remote monitoring make them easy to set up and run on any site.</p>
  <p class="copy abs" style="left:106px;top:144px;width:82px">Models cover single sets, mains failure and paralleling. Every unit is tested, supplied with wiring guides and supported by our engineers for setup questions.</p>
  <p class="copy abs" style="left:106px;top:176px;width:82px">We keep a wide range in stock with spare modules and cables, so dealers can upgrade older panels quickly and keep customers online with minimal downtime.</p>
  <div class="strip"></div><div class="pn r">01</div>
</section>

<!-- Transfer Switches -->
<section class="page switches" style="left:265px;top:882px">
  <p class="kicker abs" style="left:14px;top:18px">OUR PRODUCT</p>
  <h2 class="title abs" style="left:14px;top:32px">TRANSFER SWITCHES</h2>
  <div class="abs photo-room" style="left:92px;top:168px;width:110px;height:92px" role="img" aria-label="Switchgear installation in a plant"></div>
  <div class="abs prod" style="left:16px;top:56px;width:66px;height:186px;box-shadow:0 1px 2px rgba(0,0,0,.25)" role="img" aria-label="Grey automatic transfer switch cabinet"></div>
  <div class="abs prod" style="left:150px;top:176px;width:24px;height:28px" role="img" aria-label="Small wall-mounted switch box"></div>
  <p class="label abs" style="left:118px;top:60px">Features</p>
  <p class="copy abs" style="left:118px;top:66px;width:74px">Automatic transfer switches that move load between utility and generator in seconds. Rated from 100 to 2000 amps with open or closed transition and clear status lights.</p>
  <ul class="list abs" style="left:118px;top:104px;width:74px">
    <li>Open and closed transition models</li>
    <li>Service entrance rated options</li>
    <li>Indoor and outdoor enclosures</li>
    <li>Digital controller with event log</li>
    <li>Exerciser clock and test switch</li>
    <li>Factory tested before shipping</li>
  </ul>
  <div class="strip"></div><div class="pn l">01</div>
</section>

<!-- Distributors -->
<section class="page distributors" style="left:467px;top:882px">
  <h2 class="title abs" style="left:14px;top:24px">OUR DISTRIBUTORS</h2>
  <div class="abs" style="left:14px;top:46px;width:176px;display:flex;justify-content:space-between;align-items:center">
    <span class="brandname" style="font-size:3.2px;color:var(--gold)"><span class="mark" style="width:3px;height:3px"></span>BRIGHTLINE</span>
    <span class="brandname" style="font-size:3.4px">NORVIK<br>VELTRA</span>
    <span class="brandname" style="font-size:3.4px">ARCAND</span>
    <span class="brandname" style="font-size:3.4px;color:var(--red)">HALDEN<br>TORVEL</span>
    <span class="brandname" style="font-size:3.4px">KESTREL</span>
    <span class="brandname" style="font-size:3.4px;color:var(--red)">BRENNAN</span>
  </div>
  <div class="abs photo-sunset" style="left:0;top:66px;width:202px;height:52px" role="img" aria-label="Refinery at sunset"></div>
  <ul class="list abs" style="left:14px;top:130px;width:80px;line-height:1.6">
    <li>Buy direct from an official master distributor</li>
    <li>Buy direct from an official parts distributor</li>
    <li>Direct access to the largest stock of alternators and parts</li>
    <li>One hour response time on quotes during business hours</li>
    <li>Online library with datasheets, manuals and photos</li>
    <li>Online account with pricing, order status and history</li>
  </ul>
  <ul class="list abs" style="left:106px;top:130px;width:84px;line-height:1.6">
    <li>Quick response time for all pricing requests</li>
    <li>Standard same day shipping on stock orders</li>
    <li>Extended same day shipping on weekdays</li>
    <li>Extended cutoff on all stock orders</li>
    <li>Worldwide drop shipping available</li>
    <li>Lead referral program for qualified accounts</li>
    <li>Online training and certification program</li>
  </ul>
  <div class="strip"></div><div class="pn r">01</div>
</section>

<!-- Back page -->
<section class="page back" style="left:677px;top:882px">
  <h2 class="abs" style="left:24px;top:20px;font:700 6.5px/1 Montserrat,sans-serif;color:var(--ink)">LOREM IPSUM</h2>
  <p class="copy abs" style="left:24px;top:31px;width:156px">Brightline Energy supplies generators, alternators, parts and controls to dealers who need reliable equipment fast. Talk to our team today about stock, pricing and training.</p>
  <div class="abs photo-steel" style="left:0;top:66px;width:202px;height:124px" role="img" aria-label="Steel pipework inside a plant"></div>
  <div class="abs gold" style="left:0;top:190px;width:202px;height:70px;clip-path:polygon(0 0,100% 0,100% 10%,70% 10%,46% 100%,0 100%)"></div>
  <div class="abs brandname" style="left:16px;top:226px"><span class="mark" style="background:var(--ink)"></span>BRIGHTLINE ENERGY</div>
  <p class="abs" style="left:118px;top:216px;font-size:3px;line-height:1.4;color:var(--ink)">Brightline Energy Ltd<br>400 Harbor Way<br>Lakeview, ST 00000<br><b>1-800-555-0142</b></p>
  <p class="abs" style="left:118px;top:238px;font:600 3px/1 'Open Sans',sans-serif;color:var(--gold)">www.brightlineenergyco.example</p>
</section>

</body>
</html>
```